Summit Ridge Business Card

Side 1: Summit Ridge Logo (logo without Maltese cross) with industrial rope rescue related theme. Our company services - TRAINING - Fire Training, Confined Space Rescue Training, Rope Rescue training, Hazmat Training, Incident Command, EMS, Pump Operations Training. Website - summitridgeexample.com.
Side 2: Summit Ridge Fire Department Logo (logo with Maltese cross) with Firefighter related theme. Company (division) services - FIELD SERVICES - Fire Department, Stand-by Rescue, Safety, EMS, Planning. "Supporting the Emergency Response Community Since 1967"

Add contact information wherever it makes since (Name, Email, Phone).
I would like it to represent the Summit Ridge Fire Department Logo as a division not as a separate entity without saying it, possibly by depicting it in the background of Side 2 instead of being a standalone picture like the logo on Side 1.

```html
<!DOCTYPE html>
<html lang="en">
<head>
<meta charset="utf-8">
<title>Summit Ridge Business Card</title>
<link href="https://fonts.googleapis.com/css2?family=Archivo:wght@400;500;800&display=swap" rel="stylesheet">
<style>
  :root {
    --backdrop: #e9e7e4;
    --card: #ffffff;
    --red: #e3262c;
    --red-deep: #c71a20;
    --ink: #3c3c3c;
    --muted: #5a5a5a;
    --rule: #4a4a4a;
  }
  * { margin: 0; padding: 0; box-sizing: border-box; }
  html, body { width: 1200px; height: 779px; overflow: hidden; }
  body {
    background: var(--backdrop);
    font-family: "Archivo", Arial, sans-serif;
    color: var(--ink);
    position: relative;
  }
  .card {
    position: absolute;
    top: 240px;
    width: 520px;
    height: 298px;
    background: var(--card);
    border-radius: 18px;
    overflow: hidden;
    box-shadow: 0 10px 24px rgba(0,0,0,.18);
  }
  .card::after {
    content: "";
    position: absolute;
    left: 0; right: 0; bottom: 0;
    height: 8px;
    background: var(--red);
  }
  .card--field { left: 50px; }
  .card--training { left: 630px; }

  /* Field services side */
  .field-brand {
    position: absolute;
    top: 50px; left: 0; right: 0;
    display: flex; align-items: center; justify-content: center; gap: 12px;
  }
  .brand-mark {
    width: 22px; height: 22px;
    border-radius: 50%;
    border: 3px solid var(--red);
  }
  .brand-name {
    font-weight: 800;
    color: var(--red);
    text-transform: uppercase;
    letter-spacing: 1px;
  }
  .field-brand .brand-name { font-size: 40px; }
  .field-title {
    position: absolute; top: 146px; left: 0; right: 0;
    text-align: center;
    font-size: 22px; font-weight: 800; color: var(--red);
    letter-spacing: .5px;
  }
  .field-services {
    position: absolute; top: 186px; left: 0; right: 0;
    text-align: center; font-size: 14.5px; color: var(--muted);
  }
  .field-services .dot { color: var(--red); padding: 0 4px; }
  .field-tagline {
    position: absolute; top: 210px; left: 0; right: 0;
    text-align: center; font-size: 13.5px; color: var(--muted);
  }

  /* Training side */
  .training-brand {
    position: absolute; top: 96px; left: 26px; width: 220px;
    text-align: center;
  }
  .training-brand .brand-name { font-size: 34px; line-height: 1; }
  .divider {
    position: absolute; left: 262px; top: 40px;
    width: 1px; height: 136px; background: var(--rule);
  }
  .contact { position: absolute; left: 278px; top: 36px; width: 230px; }
  .contact-name { font-size: 19px; font-weight: 800; color: var(--red); }
  .contact-role { font-size: 13px; color: var(--muted); margin-bottom: 8px; }
  .contact-address { font-size: 12.5px; line-height: 1.3; margin-bottom: 6px; }
  .contact-list { list-style: none; font-size: 12px; line-height: 1.5; }
  .contact-list li { display: flex; align-items: center; gap: 7px; }
  .contact-list svg { width: 11px; height: 11px; flex: none; }
  .training-list {
    position: absolute; left: 26px; right: 20px; top: 208px;
    font-size: 12.5px; line-height: 1.45; color: var(--muted);
    text-align: center;
  }
  .training-list strong { font-weight: 500; color: var(--ink); }
  .edge-rule {
    position: absolute; left: 0; right: 0; bottom: 14px;
    height: 2px; background: var(--rule);
  }
</style>
</head>
<body>

<section class="card card--field" aria-label="Field services side">
  <div class="field-brand">
    <span class="brand-mark"></span>
    <span class="brand-name">Summit Ridge</span>
  </div>
  <h2 class="field-title">FIELD SERVICES</h2>
  <p class="field-services">Fire Department<span class="dot">•</span>Stand-by Rescue<span class="dot">•</span>Safety<span class="dot">•</span>EMS<span class="dot">•</span>Planning</p>
  <p class="field-tagline">Supporting the Emergency Response Community Since 1967</p>
</section>

<section class="card card--training" aria-label="Training side">
  <div class="training-brand">
    <span class="brand-name">Summit Ridge</span>
  </div>
  <div class="divider"></div>
  <div class="contact">
    <p class="contact-name">DANIEL HARPER</p>
    <p class="contact-role">President</p>
    <p class="contact-address">415 Harbor Ln., Eastport<br>TX, United States, 77000</p>
    <ul class="contact-list">
      <li><svg viewBox="0 0 12 12"><path d="M2 1l2.5 0 1 3-1.5 1c.8 1.6 1.4 2.2 3 3l1-1.5 3 1V11C5.5 11 1 6.5 2 1z" fill="var(--red)"/></svg>+1 555-010-0710</li>
      <li><svg viewBox="0 0 12 12"><rect x="3" y="0.5" width="6" height="11" rx="1" fill="none" stroke="var(--red)" stroke-width="1.4"/></svg>+1 555-010-0710</li>
      <li><svg viewBox="0 0 12 12"><rect x="0.5" y="2" width="11" height="8" fill="var(--red)"/><path d="M0.5 2l5.5 4.5L11.5 2" fill="none" stroke="#fff" stroke-width="1"/></svg>daniel@summitridgeexample.com</li>
      <li><svg viewBox="0 0 12 12"><circle cx="6" cy="6" r="5.5" fill="var(--red)"/><path d="M1 6h10M6 .5c2.5 3 2.5 8 0 11M6 .5c-2.5 3-2.5 8 0 11" fill="none" stroke="#fff" stroke-width=".8"/></svg>www.summitridgeexample.com</li>
    </ul>
  </div>
  <p class="training-list"><strong>TRAINING</strong> - Fire Training, Confined Space Rescue Training, Rope Rescue training, Hazmat Training, Incident Command, EMS, Pump Operations Training.</p>
  <div class="edge-rule"></div>
</section>

</body>
</html>
```